I would like some help creating my first business cards for my new business, I am a facilitator of a course that I have created. I am currently starting the sales promotion and marketing part of my business and need some help designing the business cards. Something fairly simple would be good, the core theme of my work is in connection of women to themselves and to each other. My initial design is a tree lit up by lights, a very mother earth type of image. This is not my design however so I probably am not legally able to use the design. I don't have a logo. Could you possibly assist with this?

I would really like to have the following details on the business card:
Meg Donlan
0431 582 917
hi.meg.donlan@larkmail.example

And also the image

Target Market(s)

Women who are living in an isolated environment

Industry/Entity Type

Counsellor

Contact Information for Business Card

Meg Donlan
Facilitator
hi.meg.donlan@larkmail.example
0431 582 917

Font styles to use
Other font styles liked:
• Handwriting - Dakota

Colors
e34197
fee18a
3276b5
33a6d7
33b8a4

Requirements
Must have
• 1) My details as above
• 2) a design (picture) that represents the mother earth theme similar to the designs included in the brief
• 3) no copyright attached to the design
• 4) Colours are very important but it is difficult to describe the colour using the colour wheel. Please refer to the example of the tree that I have included in the drop box.
• 5) I must apologise that I forgot to add the business card needs to have the name of the business in gold letters please: Riverbend Circle Gatherings Collective, thank you
Nice to have
• It would be great to use the tree design that I included in the brief, this is my favourite picture but I think it is probably copyrighted. If it's not, that is the one I would like on my business cards please.

```html
<!DOCTYPE html>
<html lang="en">
<head>
<meta charset="utf-8">
<title>Riverbend Circle Gatherings Collective – Business Card</title>
<link rel="stylesheet" href="https://fonts.googleapis.com/css2?family=Gochi+Hand&family=Open+Sans:wght@400;700&display=swap">
<style>
  :root {
    --backdrop: #b9e0d6;
    --card-light: #fffff0;
    --card-warm: #f6f8d6;
    --gold: #c49a22;
    --deep-green: #76a52a;
    --fresh-green: #a9cd45;
    --leaf-green: #9cc63b;
    --pale-green: #dfeaa8;
    --ink: #1f1f1f;
    --rule: #7ea232;
  }
  * { box-sizing: border-box; margin: 0; padding: 0; }
  html, body {
    width: 1200px;
    height: 856px;
    overflow: hidden;
    background: var(--backdrop);
  }
  .card {
    position: absolute;
    left: 60px;
    top: 118px;
    width: 1080px;
    height: 620px;
    border-radius: 48px;
    overflow: hidden;
    background: radial-gradient(ellipse at 60% 40%, var(--card-light) 0%, var(--card-warm) 100%);
    box-shadow: 0 14px 30px rgba(40, 90, 80, 0.18);
  }
  .tree-art {
    position: absolute;
    left: 80px;
    top: 100px;
    width: 370px;
    height: 420px;
    border-radius: 24px;
    background: linear-gradient(180deg,
      var(--leaf-green) 0%,
      #b3d55a 45%,
      var(--pale-green) 78%,
      rgba(246, 248, 214, 0) 100%);
  }
  .business-name {
    position: absolute;
    left: 480px;
    top: 110px;
    width: 560px;
    font-family: "Gochi Hand", cursive;
    font-weight: 400;
    font-size: 56px;
    line-height: 1.1;
    color: var(--gold);
    text-align: center;
  }
  .contact {
    position: absolute;
    left: 520px;
    top: 378px;
    width: 500px;
    font-family: "Open Sans", sans-serif;
    color: var(--ink);
  }
  .contact-rule {
    height: 2px;
    background: var(--rule);
    margin-bottom: 10px;
  }
  .person {
    display: flex;
    align-items: baseline;
    gap: 10px;
  }
  .person-name {
    font-size: 34px;
    font-weight: 700;
    color: var(--deep-green);
  }
  .person-role {
    font-size: 17px;
  }
  .contact-line {
    display: flex;
    align-items: center;
    gap: 10px;
    font-size: 22px;
    margin-top: 8px;
  }
  .contact-icon {
    width: 24px;
    height: 24px;
    flex: none;
  }
  .band-main {
    position: absolute;
    left: 0;
    bottom: 0;
    width: 880px;
    height: 44px;
    background: var(--deep-green);
  }
  .band-accent {
    position: absolute;
    right: 0;
    bottom: 0;
    width: 180px;
    height: 44px;
    background: var(--fresh-green);
  }
</style>
</head>
<body>
  <div class="card">
    <div class="tree-art" role="img" aria-label="Mother-earth illustration: a leafy green tree standing on a small grassy hill"></div>

    <h1 class="business-name">Riverbend Circle<br>Gatherings Collective</h1>

    <div class="contact">
      <div class="contact-rule"></div>
      <div class="person">
        <span class="person-name">Meg Donlan</span>
        <span class="person-role">Facilitator</span>
      </div>
      <div class="contact-line">
        <svg class="contact-icon" viewBox="0 0 24 24" aria-hidden="true">
          <circle cx="12" cy="12" r="11" fill="#9cc63b"/>
          <path d="M8 7c-1 1-1 3 1 6s4 4 5 4l2-2-2-2-1 1c-1 0-3-2-3-3l1-1-2-2z" fill="#fff"/>
        </svg>
        <span>0431 582 917</span>
      </div>
      <div class="contact-line">
        <svg class="contact-icon" viewBox="0 0 24 24" aria-hidden="true">
          <circle cx="12" cy="12" r="11" fill="#9cc63b"/>
          <rect x="6" y="8" width="12" height="8" fill="#fff"/>
          <path d="M6 8l6 5 6-5" fill="none" stroke="#9cc63b" stroke-width="1.3"/>
        </svg>
        <span>hi.meg.donlan@larkmail.example</span>
      </div>
    </div>

    <div class="band-main"></div>
    <div class="band-accent"></div>
  </div>
</body>
</html>
```